Online media outlet needs a blog and logo

A new online blog platform is being established in the UK. The blog will be very similar in layout to www.quorvel.co. It will need to have a main story slider showing three slides and block tiles beneath the slider for additional tiles.

The blog platform will be called 'Tandrel Brisk' and will also need a professional looking logo design for the name.

The website should be designed in Word Press.

Industry/Entity Type

Media

Logo Text

Tandrel Brisk

Coding

Coded - Design and coding required

Number of Pages Required

3 page

Font styles to use
Other font styles liked:
• Helvetica

Requirements
Must have
• A slider showing three slides. Be similar to Quor V (see previous comment). Be Word Press compatible.

```html
<!DOCTYPE html>
<html lang="en">
<head>
<meta charset="utf-8">
<title>Tandrel Brisk</title>
<link rel="stylesheet" href="https://fonts.googleapis.com/css2?family=Raleway:wght@400;500;600;700&family=Open+Sans:wght@400;600&display=swap">
<style>
:root{
  --black:#000;
  --white:#fff;
  --page-grey:#ebebeb;
  --ink:#333;
  --muted:#8a8a8a;
  --accent:#1a8fe0;
  --accent-deep:#0a5fa8;
  --footer-top:#0d63b3;
  --footer-bottom:#06307a;
  --footer-bar:#052a6a;
  --footer-link:#cfe0f5;
  --caption-band:rgba(40,40,40,.72);
}
*{box-sizing:border-box;margin:0;padding:0}
html,body{width:1200px;height:2362px;overflow:hidden}
body{font-family:"Raleway",Helvetica,Arial,sans-serif;background:var(--page-grey);color:var(--ink);position:relative}

/* header */
.site-header{position:absolute;left:0;top:0;width:1200px;height:87px;background:var(--black)}
.social{position:absolute;left:183px;top:26px;display:flex;gap:6px}
.social span{width:27px;height:27px;border:1.5px solid var(--white);border-radius:50%}
.brand{position:absolute;left:0;right:0;top:28px;text-align:center;color:var(--white);font-size:23px;font-weight:600;letter-spacing:.5px}
.search-icon{position:absolute;left:894px;top:32px}
.menu{position:absolute;left:948px;top:33px;display:flex;align-items:center;gap:8px;color:var(--white);font-size:12px;font-weight:500}

/* hero */
.hero{position:absolute;left:0;top:87px;width:1200px;height:467px}
.hero-photo{position:absolute;inset:0;background:linear-gradient(180deg,#6f6a62 0%,#524d48 45%,#3a3836 100%)}
.hero-caption{position:absolute;left:0;right:0;bottom:0;height:107px;background:var(--caption-band);padding:20px 0 0 173px;color:var(--white)}
.hero-caption h1{font-size:23px;font-weight:500}
.hero-caption p{font-size:14px;color:#bdbdbd;margin-top:6px}
.hero-caption .more{font-size:11px;margin-top:8px;letter-spacing:.5px}
.hero-arrow{position:absolute;top:186px}

/* tiles */
.tile{position:absolute;overflow:hidden}
.tile .photo{position:absolute;inset:0}
.tile .caption{position:absolute;left:28px;right:30px;bottom:18px;color:var(--white)}
.tile h2{font-size:18px;font-weight:500;line-height:1.25}
.tile h3{font-size:13px;font-weight:600;line-height:1.3}
.tile p{font-family:"Open Sans",Arial,sans-serif;font-size:10.5px;margin-top:5px;color:#e2e2e2}
.tile time{display:block;font-family:"Open Sans",Arial,sans-serif;font-size:10px;margin-top:5px}

/* newsletter */
.newsletter{position:absolute;left:0;top:1216px;width:1200px;height:298px}
.newsletter .photo{position:absolute;inset:0;background:linear-gradient(90deg,#5b5b60 0%,#3f4150 45%,#262a48 100%)}
.newsletter-body{position:absolute;left:0;right:0;top:72px;text-align:center;color:var(--white)}
.newsletter-body h2{font-size:22px;font-weight:400;letter-spacing:1px}
.newsletter-body p{font-size:15px;margin-top:8px}
.signup{position:absolute;left:370px;top:1372px;display:flex;gap:6px}
.signup .field{width:293px;height:41px;background:var(--white);color:#9a9a9a;font-size:13px;padding:12px 0 0 34px}
.signup .btn{width:122px;height:41px;background:var(--accent);color:var(--white);font-size:13px;font-weight:700;text-align:center;padding-top:12px}

/* feature row */
.card{position:absolute;top:1556px;height:192px}
.card-media{left:184px;width:271px;background:linear-gradient(160deg,#1c8ad6,#0c5fae);color:var(--white);padding:20px 28px 0 28px}
.card .label{font-size:12px;font-weight:600;letter-spacing:.5px}
.card-media h3{font-size:13px;font-weight:600;margin-top:14px;line-height:1.35}
.card-media p{font-family:"Open Sans",Arial,sans-serif;font-size:10px;margin-top:12px;line-height:1.6;color:#dbeaf8}
.card-media small{display:block;font-family:"Open Sans",Arial,sans-serif;font-size:10px;margin-top:10px}
.card-video{left:466px;width:271px}
.card-video .photo{position:absolute;inset:0;background:linear-gradient(180deg,#6a4a2e,#3c3a4a 55%,#7a5030)}
.card-video .label{position:absolute;left:18px;top:20px;color:var(--white);font-weight:500}
.card-video svg{position:absolute;left:106px;top:67px}
.card-gov{left:750px;width:271px;background:var(--white);border:1px solid #d8d8d8;padding:20px 18px 0 18px}
.card-gov .label{color:var(--accent-deep);font-weight:500}
.card-gov h3{font-size:14px;font-weight:500;margin-top:14px;color:#444}
.card-gov p{font-family:"Open Sans",Arial,sans-serif;font-size:10px;color:var(--muted);margin-top:10px;line-height:1.6}
.card-gov time{display:block;font-family:"Open Sans",Arial,sans-serif;font-size:10px;margin-top:14px;color:#555}
.more-chevron{position:absolute;left:586px;top:2030px}

/* footer */
.site-footer{position:absolute;left:0;top:2103px;width:1200px;height:214px;background:linear-gradient(180deg,var(--footer-top),var(--footer-bottom))}
.footer-col{position:absolute;top:44px;color:var(--white)}
.footer-col h4{font-size:12px;font-weight:700;margin-bottom:14px}
.footer-col li{list-style:none;font-family:"Open Sans",Arial,sans-serif;font-size:10.5px;color:var(--footer-link);line-height:19px}
.feed-item{display:flex;gap:12px;margin-bottom:10px;width:180px}
.feed-item i{flex:none;width:13px;height:13px;background:var(--white);border-radius:2px;margin-top:6px}
.feed-item div{font-family:"Open Sans",Arial,sans-serif;font-size:9px;line-height:14px;color:var(--white);width:150px}
.feed-item b{color:#f0c419;font-weight:400}
.most li{display:flex;gap:8px;width:200px;line-height:14px;margin-bottom:10px;color:var(--white)}
.most li::before{content:"›";font-size:14px;line-height:14px}
.footer-bar{position:absolute;left:0;top:2317px;width:1200px;height:45px;background:var(--footer-bar);color:#9fb4d8;font-family:"Open Sans",Arial,sans-serif;font-size:10px;padding:14px 0 0 198px}
</style>
</head>
<body>

<header class="site-header">
  <div class="social"><span></span><span></span><span></span><span></span></div>
  <div class="brand">TANDREL BRISK</div>
  <svg class="search-icon" width="20" height="20" viewBox="0 0 20 20"><circle cx="8" cy="8" r="6" fill="none" stroke="#fff" stroke-width="2.4"/><line x1="12.5" y1="12.5" x2="18" y2="18" stroke="#fff" stroke-width="2.6" stroke-linecap="round"/></svg>
  <div class="menu"><svg width="22" height="14" viewBox="0 0 22 14"><path d="M0 1h22M0 7h22M0 13h22" stroke="#fff" stroke-width="1.8"/></svg>MENU</div>
</header>

<section class="hero">
  <div class="hero-photo" role="img" aria-label="Busy pedestrian shopping street with people walking towards the camera"></div>
  <svg class="hero-arrow" style="left:178px" width="20" height="48" viewBox="0 0 20 48"><path d="M17 2 3 24l14 22" fill="none" stroke="#fff" stroke-width="2"/></svg>
  <svg class="hero-arrow" style="left:1000px" width="20" height="48" viewBox="0 0 20 48"><path d="M3 2l14 22L3 46" fill="none" stroke="#fff" stroke-width="2"/></svg>
  <div class="hero-caption">
    <h1>Aenean porttitor eros vel dolor</h1>
    <p>Aiaculis facilisis massa Etiam eu urna Sed porta Suspendisse quam leo</p>
    <div class="more">LEARN MORE</div>
  </div>
</section>

<article class="tile" style="left:183px;top:589px;width:553px;height:353px">
  <div class="photo" role="img" aria-label="Camera crew interviewing a politician with a microphone" style="background:linear-gradient(160deg,#9aa8b8 0%,#5d5f66 50%,#2b2d33 100%)"></div>
  <div class="caption" style="left:35px;bottom:20px"><h2>Aenean porttitor eros vel dolor Donec convallis pede</h2><p>Aiaculis facilisis massa Etiam eu urna Sed porta Suspendisse quam leo</p><time>25 APRIL 2016</time></div>
</article>
<article class="tile" style="left:747px;top:589px;width:274px;height:172px">
  <div class="photo" role="img" aria-label="Speaker addressing a packed conference hall" style="background:linear-gradient(150deg,#4a4f66,#8a5a4a 60%,#5a4038)"></div>
  <div class="caption" style="left:20px;right:16px;bottom:16px"><h3>Sed porta Suspendisse</h3><p>Morbi ut mi Nullam enim leo egestas condime</p><time>10 APRIL 2016</time></div>
</article>
<article class="tile" style="left:747px;top:770px;width:274px;height:172px">
  <div class="photo" role="img" aria-label="Reporters holding microphones toward a speaker" style="background:linear-gradient(160deg,#3a2f33,#1f1d20 60%,#2c2a2c)"></div>
  <div class="caption" style="left:16px;right:16px;bottom:16px"><h3>Morbi porta libero id ullamcorper nonummy nibh ligula</h3><time>10 APRIL 2016</time></div>
</article>
<article class="tile" style="left:183px;top:959px;width:271px;height:208px">
  <div class="photo" role="img" aria-label="Press photographers crowding at night under flash lights" style="background:linear-gradient(160deg,#6a4a2a,#2e2018 55%,#1a1412)"></div>
  <div class="caption"><h3>Duis quam Nam eget lacus<br>Aliquam erat volutpat</h3><time>25 APRIL 2016</time></div>
</article>
<article class="tile" style="left:465px;top:959px;width:271px;height:208px">
  <div class="photo" role="img" aria-label="Politician speaking at a podium in front of flags" style="background:linear-gradient(160deg,#3a3e48,#2a2a30 55%,#4a3a30)"></div>
  <div class="caption" style="left:23px"><h3>Vivamus porttitor neque at<br>volutpat rutrum purus</h3><time>25 APRIL 2016</time></div>
</article>
<article class="tile" style="left:748px;top:959px;width:271px;height:208px">
  <div class="photo" role="img" aria-label="Candidate at a campaign rally with flags behind" style="background:linear-gradient(160deg,#2a3a6a,#4a3050 55%,#22253a)"></div>
  <div class="caption" style="left:23px"><h3>Pellentesque rutrum malesuada<br>neque Nunc</h3><time>25 APRIL 2016</time></div>
</article>

<section class="newsletter">
  <div class="photo" role="img" aria-label="Domed parliament building with columns at dusk"></div>
  <div class="newsletter-body">
    <h2>JOIN OUR NEWSLETTER</h2>
    <p>Sign up to our email briefings for latest news &amp; blog updates</p>
  </div>
</section>
<div class="signup"><div class="field">Email address</div><div class="btn">SUBSCRIBE</div></div>

<article class="card card-media">
  <div class="label">MEDIA</div>
  <h3>Cras a ante vitae enim iaculis aliquam Mauris nunc</h3>
  <p>habitant morbi tristique senectus et netus et malesuada fames ac turpis egestas Cras id elit Integer quis urna Ut ant</p>
  <small>Posted 2 days ago</small>
</article>
<article class="card card-video">
  <div class="photo" role="img" aria-label="Man in a suit giving two thumbs up"></div>
  <div class="label">WATCH RECENT VIDEO</div>
  <svg width="60" height="60" viewBox="0 0 60 60"><circle cx="30" cy="30" r="27" fill="none" stroke="#fff" stroke-width="2.5"/><path d="M23 17v26l21-13z" fill="#fff"/></svg>
</article>
<article class="card card-gov">
  <div class="label">UK GOVERNMENT</div>
  <h3>Dis parturient montes nascetur</h3>
  <p>Aabitant morbi tristique senectus et netus et malesuada fames ac turpis egestas Cras id elit Integer quis urna Ut ant</p>
  <time>15 April 2016</time>
</article>

<article class="tile" style="left:184px;top:1764px;width:410px;height:238px">
  <div class="photo" role="img" aria-label="Refugees in life jackets arriving on a shore" style="background:linear-gradient(160deg,#7a7060,#a86a3a 50%,#3a3530)"></div>
  <div class="caption" style="left:28px;bottom:20px"><h2>Aenean porttitor eros vel dolor</h2><p>Aiaculis facilisis massa Etiam eu urna Sed porta Suspendisse quam leo</p><time>25 APRIL 2016</time></div>
</article>
<article class="tile" style="left:608px;top:1764px;width:411px;height:238px">
  <div class="photo" role="img" aria-label="Politician speaking at a microphone against a blue backdrop" style="background:linear-gradient(160deg,#1e3a8a,#2a4aa0 50%,#1a2a6a)"></div>
  <div class="caption" style="left:25px;bottom:20px"><h2>Mauris vel lacus vitae felis vestibulum</h2><p>Aiaculis facilisis massa Etiam eu urna Sed porta Suspendisse quam leo</p><time>25 APRIL 2016</time></div>
</article>

<svg class="more-chevron" width="30" height="18" viewBox="0 0 30 18"><path d="M2 2l13 13L28 2" fill="none" stroke="#8c8c8c" stroke-width="3.5"/></svg>

<footer class="site-footer">
  <div class="footer-col" style="left:183px"><h4>COMPANY</h4><ul><li>Home</li><li>Stocks</li><li>Currences</li><li>Politics</li></ul></div>
  <div class="footer-col" style="left:311px"><h4>SUBLINKS</h4><ul><li>Phasellus felis</li><li>celerisque</li><li>Tempus eget</li><li>Lobortis</li></ul></div>
  <div class="footer-col" style="left:449px"><h4>LATEST POSTS</h4><ul><li>Phasellus felis</li><li>Dolor celerisque</li><li>Tempus eget</li><li>Lobortis</li></ul></div>
  <div class="footer-col" style="left:598px"><h4>SOCIAL FEED</h4>
    <div class="feed-item"><i></i><div><b>@BriskReader</b> susct varius mi.<br>Cum sociis natoque penatbus et<br>1 day ago</div></div>
    <div class="feed-item"><i></i><div><b>@BriskReader</b> susct varius mi.<br>Cum sociis natoque penatbus et<br>1 day ago</div></div>
  </div>
  <div class="footer-col" style="left:828px"><h4>MOST VIEWED</h4>
    <ul class="most"><li>Nam eget lacus Aliquam erat volutpat Quisque dignissim</li><li>Congue leo Mauris vel lacus vitae felis vestibulum volutpat Etiam</li><li>Est nunc venenatis in tristique eu</li></ul>
  </div>
</footer>
<div class="footer-bar">© 2015 Company Name. All right reserved. Term of Use</div>

</body>
</html>
```